Satchel & Sundial needs new business card design

I need a new business card design. I'm looking for out-of-the-box design which represents the freedom of being a location independent entrepreneur.
I offer coaching, retreats and trips.
I would like to see designs with and without the photo.
Colors I use are black (#000000), green (#25A796) and brown (#D7C38C)
Website satchelandsundial.example

Target Market(s)

location independent entrepreneurs, digital nomads, people looking to swap the 9 to 5 for a lifestyle business

Industry/Entity Type

Business

Contact Information for Business Card

Dorota Falkner
Your Lifestyle Business Coach, Retreat & Trip Leader
http://satchelandsundial.example
hello@satchelandsundial.example
Live a life you don't need a holiday from

Font styles to use
Serif
Sans Serif

Requirements
Must have
• One side should contain only the logo. I would also consider having the "Live a life you don't need a holiday from" on that side too (depending on how it looks)
• Please show both sides on the designs.

```html
<!DOCTYPE html>
<html lang="en">
<head>
<meta charset="utf-8">
<title>Satchel &amp; Sundial – Business Card</title>
<link rel="stylesheet" href="https://fonts.googleapis.com/css2?family=Oswald:wght@300;400;500;600&family=Roboto:wght@400&display=swap">
<style>
  :root {
    --backdrop: #e8e8e8;
    --gold: #d2bd84;
    --gold-deep: #c9b27a;
    --ink: #111111;
    --teal: #1f9a89;
    --teal-text: #1a8f80;
    --paper: #f6f6f6;
    --paper-shade: #e4e4e4;
    --band: #141414;
    --band-text: #f2f2f2;
  }
  * { box-sizing: border-box; margin: 0; padding: 0; }
  html, body {
    width: 1200px; height: 576px; overflow: hidden;
    background: var(--backdrop);
  }
  .stage { position: relative; width: 1200px; height: 576px; }

  .card {
    position: absolute; top: 138px;
    width: 482px; height: 294px;
    border-radius: 8px; overflow: hidden;
  }

  /* Front: logo side */
  .card-front {
    left: 82px;
    background: linear-gradient(180deg, var(--gold) 0%, var(--gold-deep) 100%);
    display: flex; align-items: center; justify-content: center;
  }
  .brand-name {
    font-family: "Oswald", sans-serif;
    font-weight: 500;
    font-size: 40px;
    letter-spacing: 1px;
    text-transform: uppercase;
    color: var(--ink);
    margin-top: -14px;
  }

  /* Back: contact side */
  .card-back { left: 602px; width: 480px; }
  .card-back svg.card-art { position: absolute; inset: 0; }

  .contact-name {
    position: absolute; left: 263px; top: 50px;
    font-family: "Oswald", sans-serif; font-weight: 600;
    font-size: 21px; letter-spacing: 0.3px;
    color: var(--ink); text-transform: uppercase;
  }
  .contact-role {
    position: absolute; left: 263px; top: 80px;
    font-family: "Oswald", sans-serif; font-weight: 400;
    font-size: 11.5px; line-height: 15px;
    color: var(--teal-text);
  }
  .contact-list {
    position: absolute; left: 263px; top: 141px;
    list-style: none;
    font-family: "Oswald", sans-serif; font-weight: 300;
    font-size: 12.5px; color: var(--ink);
  }
  .contact-list li { display: flex; align-items: center; height: 20px; margin-bottom: 0.5px; }
  .contact-list .icon { width: 11px; height: 11px; margin-right: 7px; flex: none; }
  .contact-list .accent { color: var(--teal-text); font-weight: 400; }
  .social-mark { width: 9px; height: 9px; background: var(--ink); margin-right: 7px; flex: none; }

  .tagline {
    position: absolute; left: 232px; top: 263px; width: 240px;
    font-family: "Roboto", sans-serif; font-size: 12.5px;
    color: var(--band-text); text-align: center;
  }
</style>
</head>
<body>
<main class="stage">

  <section class="card card-front" aria-label="Card front">
    <span class="brand-name">Satchel &amp; Sundial</span>
  </section>

  <section class="card card-back" aria-label="Card back">
    <svg class="card-art" width="480" height="294" viewBox="0 0 480 294" aria-hidden="false">
      <defs>
        <linearGradient id="paper" x1="0" y1="0" x2="1" y2="1">
          <stop offset="0" stop-color="#f8f8f8"/>
          <stop offset="1" stop-color="#e2e2e2"/>
        </linearGradient>
        <linearGradient id="portrait" x1="0" y1="0" x2="0" y2="1">
          <stop offset="0" stop-color="#7c9470"/>
          <stop offset="0.55" stop-color="#8f9a7a"/>
          <stop offset="1" stop-color="#7d6f56"/>
        </linearGradient>
      </defs>
      <rect class="paper" width="480" height="294" fill="url(#paper)"/>
      <path class="portrait-area" role="img" aria-label="Photo of the coach standing among trees, holding a small chalkboard sign"
            d="M0 0 H198 C224 80 232 200 204 294 H0 Z" fill="url(#portrait)"/>
      <path class="curve-stripe" d="M198 0 H206 C236 80 242 200 214 294 H204 C232 200 224 80 198 0 Z" fill="var(--teal)"/>
      <polygon class="gold-strip" points="0,275 210,275 204,294 0,294" fill="var(--gold)"/>
      <polygon class="tagline-band" points="216,254 480,254 480,294 200,294" fill="var(--band)"/>
    </svg>

    <h1 class="contact-name">Dorota Falkner</h1>
    <p class="contact-role">Your Lifestyle Business Coach<br>Retreat &amp; Trip Leader</p>

    <ul class="contact-list">
      <li>
        <svg class="icon" viewBox="0 0 12 12"><rect x="0.5" y="2" width="11" height="8" fill="var(--teal)"/><path d="M0.5 2 L6 6.5 L11.5 2" fill="none" stroke="#fff" stroke-width="1"/></svg>
        hello@satchelandsundial.example
      </li>
      <li>
        <svg class="icon" viewBox="0 0 12 12"><circle cx="6" cy="6" r="5" fill="none" stroke="var(--teal)" stroke-width="1.2"/><ellipse cx="6" cy="6" rx="2.2" ry="5" fill="none" stroke="var(--teal)" stroke-width="1"/><line x1="1" y1="6" x2="11" y2="6" stroke="var(--teal)" stroke-width="1"/></svg>
        <span>www.<span class="accent">satchelandsundial</span>.example</span>
      </li>
      <li>
        <span class="social-mark"></span>
        <span class="accent">/satchelandsundial</span>
      </li>
    </ul>

    <p class="tagline">Live a life you don't need a holiday from</p>
  </section>

</main>
</body>
</html>
```